Candle Rental Business seeks new website design

We need a new website design for a Candle hire business. The business rents out pillar candles for events such as weddings and corporate events. Our main target market is weddings. The business name is Hire a Lantern. The business name does not have a logo design.

We would like a website that is light in colours and creates a warm atmosphere. The design needs to be elegant and upmarket. There are different size candles that we hire out, ranging from 10cm diameter to 20cm diameter, flat, tall etc. All our candles are white in colour. Its just the size that differs.

We would also like to include a section for hiring out decor such as glassvases, candlebras, overlays and chairs sachets, chair covers. However, this is not the businesses main focus but an additional offering to customers.

Target Market(s)

Wedding venues and brides. Corporate events. School dances.

Industry/Entity Type

Hospitality

Logo Text

Hire a Lantern

Number of Pages Required

1 page

Font styles to use
Sans Serif
Script

Requirements
Must have
• Pictures of pillar candles. Plain white candles. The website must centre around candles.
Nice to have
• Different examples of candle centrepieces
Should not have
• Pictures must not be of brides. Pictures of surrounding is perferable.

```html
<!DOCTYPE html>
<html lang="en">
<head>
<meta charset="utf-8">
<title>Hire a Lantern</title>
<link rel="stylesheet" href="https://fonts.googleapis.com/css2?family=Questrial&family=Lato:ital,wght@0,400;0,700;1,400&display=swap">
<style>
:root{
  --pink:#d0789f;
  --pink-soft:#e39bbd;
  --purple:#9a6fbe;
  --purple-light:#ad87cf;
  --ink:#1d1d1d;
  --text:#3a3a3a;
  --muted:#8a8a8a;
  --white:#ffffff;
  --hero-dark:#2b211c;
  --footer:#2c2c2c;
  --footer-dark:#222222;
  --footer-text:#cfcfcf;
  --rule:#dedede;
}
*{box-sizing:border-box;margin:0;padding:0}
html,body{width:1200px;height:2651px;overflow:hidden}
body{font-family:"Lato",sans-serif;color:var(--text);background:var(--white);position:relative}
.abs{position:absolute}
.head{font-family:"Questrial",sans-serif}

/* hero */
.hero{position:absolute;left:0;top:0;width:1200px;height:656px;
  background:radial-gradient(ellipse at 55% 45%,#f6e6cf 0%,#b59a7e 22%,#5e4a3c 48%,#2a211c 80%);}
.topbar{position:absolute;left:0;top:0;width:1200px;height:100px;background:rgba(30,24,20,.55)}
.brand{position:absolute;left:132px;top:34px;display:flex;align-items:center;gap:14px;color:var(--white);font-family:"Questrial",sans-serif;font-size:38px}
.brand-mark{width:30px;height:30px;border-radius:50%;background:var(--white)}
.nav{position:absolute;left:495px;top:58px;display:flex;gap:0;font-size:14px;color:var(--white)}
.nav a{color:var(--white);text-decoration:none;margin-right:44px;position:relative}
.nav a.active::after{content:"";position:absolute;left:-2px;right:-2px;top:22px;height:3px;background:var(--white)}
.phone{position:absolute;left:915px;top:18px;display:flex;align-items:center;gap:10px;color:var(--pink-soft);font-size:18px}
.phone i{width:26px;height:26px;border-radius:50%;background:var(--pink);display:flex;align-items:center;justify-content:center}
.arrow{position:absolute;top:285px}
.caption{position:absolute;left:0;top:592px;width:1200px;height:64px;background:rgba(20,15,12,.45);
  color:var(--white);font-family:"Questrial",sans-serif;font-size:31px;padding-left:132px;line-height:64px}

/* features */
.feature{position:absolute;top:693px;width:267px;height:134px;border-radius:6px;
  background:linear-gradient(180deg,#6b5f5e,#2f2828);box-shadow:0 10px 14px -8px rgba(0,0,0,.5);color:var(--white)}
.feature .icon{position:absolute;left:22px;top:22px;width:70px;height:90px;border-radius:6px;background:rgba(255,255,255,.25)}
.feature h3{position:absolute;left:120px;top:22px;font-family:"Questrial",sans-serif;font-weight:400;font-size:21px;line-height:24px;color:#eee}
.feature .more{position:absolute;left:120px;top:78px;border:1px solid var(--white);padding:4px 14px;font-size:14px;font-weight:700}

/* welcome */
.welcome h2{position:absolute;left:132px;top:884px;font-family:"Questrial",sans-serif;font-weight:400;font-size:29px;color:var(--ink)}
.welcome h2 b{font-family:"Lato",sans-serif;font-weight:700;letter-spacing:1px}
.welcome .rule{position:absolute;left:132px;top:930px;width:532px;height:1px;background:var(--rule)}
.welcome .rule::before{content:"";position:absolute;left:0;top:-1px;width:108px;height:3px;background:var(--pink)}
.welcome p{position:absolute;left:132px;top:947px;width:534px;font-size:13px;line-height:19px;color:var(--text)}
.btn-pink{position:absolute;left:132px;top:1085px;width:112px;height:37px;background:var(--pink);color:var(--white);font-size:14px;font-weight:700;text-align:center;line-height:37px;border-radius:2px}
.video{position:absolute;left:739px;top:901px;width:330px;height:221px;border-radius:6px;overflow:hidden;
  background:linear-gradient(135deg,#7b6a64,#3a302e);border:2px solid #222}
.video .play{position:absolute;left:145px;top:80px;width:50px;height:36px;background:#d8251f;border-radius:8px}
.video .play::after{content:"";position:absolute;left:20px;top:10px;border-left:14px solid #fff;border-top:8px solid transparent;border-bottom:8px solid transparent}
.video .bar{position:absolute;left:0;bottom:0;width:100%;height:30px;background:#1b1b1b}
.video .track{position:absolute;left:62px;bottom:12px;width:180px;height:5px;background:#555;border-radius:3px}
.video .track::before{content:"";position:absolute;left:0;top:0;width:82px;height:5px;background:#c7221d;border-radius:3px}

/* decor */
.decor{position:absolute;left:0;top:1179px;width:1200px;height:311px;
  background:radial-gradient(circle at 80% 40%,var(--purple-light),var(--purple) 60%)}
.decor h2{position:absolute;left:0;width:1200px;top:38px;text-align:center;font-family:"Questrial",sans-serif;font-weight:400;font-size:27px;color:var(--white)}
.decor h2 b{font-weight:700}
.decor .rule{position:absolute;left:428px;top:86px;width:344px;height:1px;background:rgba(255,255,255,.6)}
.decor-item{position:absolute;top:134px;width:200px;margin-left:-100px;text-align:center;color:var(--white);font-weight:700;font-size:18px}
.decor-item .circle{width:76px;height:76px;border-radius:50%;border:2px solid var(--white);margin:0 auto 18px;background:rgba(255,255,255,.08)}
.decor-item.on .circle{background:#f2a3c8}
.decor .sep{position:absolute;top:132px;width:1px;height:130px;background:rgba(255,255,255,.35)}

/* testimonials */
.testi-title{position:absolute;left:0;width:1200px;top:1547px;text-align:center;font-family:"Questrial",sans-serif;font-size:27px;color:var(--ink)}
.testi-title b{font-weight:700}
.testi-rule{position:absolute;left:424px;top:1593px;width:352px;height:1px;background:var(--rule)}
.testi-rule::before{content:"";position:absolute;left:112px;top:-1px;width:128px;height:3px;background:var(--pink)}
.card{position:absolute;top:1624px;width:432px}
.card .avatar{width:92px;height:92px;border-radius:50%;border:4px solid var(--pink);background:linear-gradient(#c9b7a9,#8e7a6c)}
.card .name{position:absolute;left:116px;top:24px;font-size:14px;font-weight:700;color:#1e2f4f}
.card .role{position:absolute;left:116px;top:44px;font-size:12px;color:var(--pink)}
.card p{margin-top:18px;font-style:italic;font-size:13px;line-height:26px;color:var(--text)}
.card .q{font-family:"Questrial",sans-serif;color:#bbb;font-size:30px;font-style:normal;line-height:0}
.vsep{position:absolute;left:599px;top:1630px;width:1px;height:210px;background:var(--rule)}
.dots{position:absolute;left:554px;top:1867px;display:flex;gap:11px}
.dots i{width:16px;height:16px;border-radius:50%;background:#222;border:2px solid #222}
.dots i.off{background:#fff}

/* cta */
.cta{position:absolute;left:0;top:1949px;width:1200px;height:375px;
  background:radial-gradient(ellipse at 33% 45%,#e9e0d6 0%,#8b7f76 25%,#3a3432 60%,#211d1c 100%)}
.cta-text{position:absolute;left:511px;top:68px;color:var(--white)}
.cta-text h3{font-size:25px;font-weight:700;letter-spacing:1px}
.cta-text .sub{font-size:21px;line-height:30px;width:560px}
.cta-text .sizes{margin-top:14px;font-size:19px;font-weight:700;line-height:27px}
.cta-btn{display:inline-block;margin-top:20px;border:1px solid var(--white);width:150px;height:50px;line-height:50px;text-align:center;font-size:19px}

/* footer */
.footer{position:absolute;left:0;top:2324px;width:1200px;height:327px;background:var(--footer);color:var(--footer-text);font-size:12px}
.footer .line{position:absolute;left:0;top:60px;width:1200px;height:1px;background:#444}
.footer h4{position:absolute;top:24px;font-family:"Questrial",sans-serif;font-weight:400;font-size:17px;color:#e5e5e5}
.links{position:absolute;left:132px;top:76px;list-style:none}
.links li{margin-bottom:13px;color:#ddd}
.links li::before{content:"›";margin-right:14px;color:#999}
.news{position:absolute;left:306px;top:78px;width:240px}
.news .row{display:flex;gap:10px;margin-bottom:10px;line-height:15px}
.news .date{width:22px;height:27px;background:#555;color:#fff;font-size:11px;font-weight:700;text-align:center;flex-shrink:0;padding-top:2px}
.news .t{color:var(--purple-light);font-weight:700}
.contact{position:absolute;left:602px;top:78px;line-height:19px}
.contact b{color:#fff}
.contact .ci{display:flex;align-items:center;gap:10px;margin-top:16px}
.form{position:absolute;left:848px;top:78px;width:221px}
.form .f{height:30px;background:#1c1c1c;border:1px solid #3c3c3c;margin-bottom:7px;padding:7px 8px;color:#888;font-size:11px}
.form .f.msg{height:66px}
.submit{width:98px;height:30px;background:var(--purple);color:#fff;font-weight:700;font-size:14px;text-align:center;line-height:30px;margin-top:3px}
.bottom{position:absolute;left:0;top:276px;width:1200px;height:51px;background:var(--footer-dark)}
.bottom .copy{position:absolute;left:132px;top:13px;color:#ddd}
.bottom .rule{position:absolute;left:132px;top:0;width:937px;height:1px;background:#444}
.social{position:absolute;left:954px;top:10px;display:flex;gap:6px}
.social i{width:22px;height:22px;background:#555;border-radius:3px}
.social i:first-child{background:var(--purple)}
</style>
</head>
<body>

<section class="hero" role="img" aria-label="Glowing white pillar candles in clear glass holders on a wooden table">
</section>
<header class="topbar"></header>
<div class="brand"><span class="brand-mark"></span>Hire a Lantern</div>
<nav class="nav head">
  <a class="active">Home</a><a>About Us</a><a>Our Products</a><a>Hire Candles</a><a>Décor Hire</a><a>Contact Us</a>
</nav>
<div class="phone"><i><svg width="14" height="14" viewBox="0 0 24 24"><path fill="#fff" d="M6.6 10.8a15 15 0 0 0 6.6 6.6l2.2-2.2c.3-.3.7-.4 1-.2 1.1.4 2.3.6 3.6.6.6 0 1 .4 1 1V20c0 .6-.4 1-1 1A17 17 0 0 1 3 4c0-.6.4-1 1-1h3.5c.6 0 1 .4 1 1 0 1.3.2 2.5.6 3.6.1.3 0 .7-.2 1z"/></svg></i>(555)0142-318</div>
<svg class="arrow" style="left:56px" width="28" height="84" viewBox="0 0 28 84"><path d="M26 2 2 42l24 40" stroke="#fff" stroke-width="2" fill="none" opacity=".8"/></svg>
<svg class="arrow" style="left:1116px" width="28" height="84" viewBox="0 0 28 84"><path d="M2 2l24 40L2 82" stroke="#fff" stroke-width="2" fill="none" opacity=".8"/></svg>
<div class="caption">Creating A Warm Atmosphere &amp; Special Touch To All Occasions</div>

<div class="feature" style="left:159px"><div class="icon" role="img" aria-label="Hire candles icon"></div><h3>Hire<br>Candles</h3><span class="more">Read More</span></div>
<div class="feature" style="left:466px"><div class="icon" role="img" aria-label="Personalised candle icon"></div><h3>Personalised<br>Candles</h3><span class="more">Read More</span></div>
<div class="feature" style="left:772px"><div class="icon" role="img" aria-label="Décor hire icon"></div><h3>Décor<br>Hire</h3><span class="more">Read More</span></div>

<section class="welcome">
  <h2>Welcome to <b>HIRE A LANTERN</b></h2>
  <div class="rule"></div>
  <p>Lorem ipsum dolor sit amet, consectetur adipiscing elit. Nulla in sollicitudin velit, bibendum velit. Cras vel facilisis ipsum, et venenatis risus. In egestas nunc etvb eros auctor sollicitu Etiam ut enim vitae magna volutpat venenatis vitae nonprof diam. Nam nunc velit, tristique a sapien euismod, pulvinar vestibulum dui. Morbi porttitor eu erat imperdiet pretium consequat fcilelis. Cras vel facilisis ipsum, et venenatis risus. In egestas nunc etvb eros auctor sollicitu.</p>
  <div class="btn-pink">READ MORE</div>
  <div class="video" role="img" aria-label="Video of candles on a lounge table">
    <div class="play"></div><div class="bar"><div class="track"></div></div>
  </div>
</section>

<section class="decor">
  <h2>Our Decor <b>Hires</b></h2>
  <div class="rule"></div>
  <div class="decor-item" style="left:251px"><div class="circle" role="img" aria-label="Glass vase icon"></div>Glass Vases</div>
  <div class="sep" style="left:385px"></div>
  <div class="decor-item on" style="left:497px"><div class="circle" role="img" aria-label="Candle bar icon"></div>Candle Bars</div>
  <div class="sep" style="left:609px"></div>
  <div class="decor-item" style="left:733px"><div class="circle" role="img" aria-label="Chair sachet icon"></div>Chair Sachets</div>
  <div class="sep" style="left:846px"></div>
  <div class="decor-item" style="left:942px"><div class="circle" role="img" aria-label="Chair cover icon"></div>Chair Covers</div>
</section>

<h2 class="testi-title">Client <b>Testimonials</b></h2>
<div class="testi-rule"></div>
<div class="card" style="left:132px">
  <div class="avatar" role="img" aria-label="Client portrait"></div>
  <div class="name">Mr. Arlen Castell</div><div class="role">Lorem Ipsum</div>
  <p><span class="q">“</span> Utm tellus dolor, dapibus eget, elemen velmki cursus eleifelita arnean auctorbni wisi et urnam. Lorem ipsum dolor sit amet, conse ctetur adipiscing elit. Nulla in sollicitudin velit, bibendum velit.Cras vel facilisis ipsum, et venenatis risus. <span class="q" style="float:right">”</span></p>
</div>
<div class="vsep"></div>
<div class="card" style="left:636px">
  <div class="avatar" role="img" aria-label="Client portrait"></div>
  <div class="name">Mr. Arlen Castell</div><div class="role">Lorem Ipsum</div>
  <p><span class="q">“</span> Utm tellus dolor, dapibus eget, elemen velmki cursus eleifelita arnean auctorbni wisi et urnam. Lorem ipsum dolor sit amet, conse ctetur adipiscing elit. Nulla in sollicitudin velit, bibendum velit.Cras vel facilisis ipsum, et venenatis risus. <span class="q" style="float:right">”</span></p>
</div>
<div class="dots"><i></i><i class="off"></i><i></i><i></i></div>

<section class="cta" role="img" aria-label="A lit white candle in a beaded holder among festive decorations">
  <div class="cta-text">
    <h3>We DESIGN, MANUFACTURE &amp; PERSONALISE</h3>
    <div class="sub">All Of Our CANDLES In Our Most Distinctive Handcrafted Manner!</div>
    <div class="sizes">Different Size Candles Ranging From<br>10cm Diameter To 20cm Diameter, Flat, Tall Etc</div>
    <div class="cta-btn">BUY NOW</div>
  </div>
</section>

<footer class="footer">
  <h4 style="left:132px">Quick Links</h4>
  <h4 style="left:306px">News / Updates</h4>
  <h4 style="left:602px">Contact Detail</h4>
  <h4 style="left:848px">Quick Contact</h4>
  <div class="line"></div>
  <ul class="links"><li>Home</li><li>About Us</li><li>Our Products</li><li>Hire Candles</li><li>Décor Hire</li><li>Contact Us</li></ul>
  <div class="news">
    <div class="row"><span class="date">22</span><div><span class="t">Duis autem vel eumsodn</span><br>Lorem ipsum dolor sit ametn nk consectetuer adipiscing elit.</div></div>
    <div class="row"><span class="date">22</span><div><span class="t">Duis autem vel eumsodn</span><br>Lorem ipsum dolor sit ametn nk consectetuer adipiscing elit.</div></div>
    <div class="row"><span class="date">22</span><div><span class="t">Duis autem vel eumsodn</span><br>Lorem ipsum dolor sit ametn nk consectetuer adipiscing elit.</div></div>
  </div>
  <div class="contact">
    <b>Hire a Lantern</b><br>24 Lumen Lane, Wick<br>Street no-40512
    <div class="ci"><svg width="14" height="14" viewBox="0 0 24 24"><path fill="#bbb" d="M6.6 10.8a15 15 0 0 0 6.6 6.6l2.2-2.2c.3-.3.7-.4 1-.2 1.1.4 2.3.6 3.6.6.6 0 1 .4 1 1V20c0 .6-.4 1-1 1A17 17 0 0 1 3 4c0-.6.4-1 1-1h3.5c.6 0 1 .4 1 1 0 1.3.2 2.5.6 3.6.1.3 0 .7-.2 1z"/></svg>555-014-2318</div>
    <div class="ci"><svg width="14" height="14" viewBox="0 0 24 24"><rect x="6" y="3" width="12" height="6" fill="#bbb"/><rect x="3" y="9" width="18" height="8" rx="1" fill="#bbb"/><rect x="6" y="14" width="12" height="7" fill="#888"/></svg>555-014-2390</div>
    <div class="ci"><svg width="14" height="12" viewBox="0 0 24 18"><rect x="1" y="1" width="22" height="16" fill="none" stroke="#bbb" stroke-width="2"/><path d="M1 1l11 9 11-9" fill="none" stroke="#bbb" stroke-width="2"/></svg>hello@hirealantern.com</div>
  </div>
  <div class="form">
    <div class="f">Name</div><div class="f">Email</div><div class="f msg">Message</div>
    <div class="submit">SUBMIT</div>
  </div>
  <div class="bottom">
    <div class="rule"></div>
    <div class="copy">Copyright © 2016 HIRE A LANTERN | All Rights Reserved.</div>
    <div class="social"><i></i><i></i><i></i><i></i></div>
  </div>
</footer>

</body>
</html>
```